Turm7Zwerge
Zielgruppe
Zielgruppe sind die Eltern, Lehrer, Kindergärtner, aber auch Kinder, die bereits Lesen können.
Aufgabenstellung
Ich brauche einen Flyer und ein Plakat für eine Kinderschachschule für Kinder zwischen 4 und 15 Jahren. Auf dem Flyer, den ich in A6-Format drucken möchte (beidseitig), muss ich die Info über die Kinderschachschule Turm7Zwerge (mehr Infos unter www.turm7zwerge-beispiel.ch), dh., was wir machen, Kontaktdaten, etc schreiben können. Es dient als Werbematerial zum Auslegen
Auf dem Plakat wird mehr oder weniger das Gleiche stehen, es wird jedoch als Din A4 Seite aufgehängt.
Unsere Kontaktinformation ist wie folgt:
Turm7Zwerge: Züge für Wolkenkinder
www.turm7zwerge-beispiel.ch

```html
<!DOCTYPE html>
<html lang="de">
<head>
<meta charset="utf-8">
<title>Turm7Zwerge – Flyer</title>
<link rel="stylesheet" href="https://fonts.googleapis.com/css2?family=Cabin:wght@400;700&display=swap">
<style>
  :root {
    --backdrop: #e4e4e4;
    --paper: #ffffff;
    --ink: #1e1e1e;
    --orange: #f29a1f;
    --orange-light: #fbc463;
    --brand: #2c2c6e;
    --photo-warm: #b08a5e;
    --photo-dark: #5a4a3c;
    --board-grey: #d9d9d9;
  }
  * { box-sizing: border-box; margin: 0; padding: 0; }
  html, body { width: 1200px; height: 1200px; overflow: hidden; }
  body {
    background: var(--backdrop);
    font-family: "Cabin", "Gill Sans", sans-serif;
    color: var(--ink);
  }
  .flyer {
    position: absolute;
    left: 190px; top: 20px;
    width: 820px; height: 1160px;
    background: var(--paper);
    box-shadow: 0 6px 24px rgba(0,0,0,.18);
    overflow: hidden;
  }
  .brand {
    position: absolute; left: 40px; top: 28px;
    display: flex; align-items: center; gap: 10px;
  }
  .brand-mark { width: 26px; height: 26px; background: var(--orange); }
  .brand-name { font-size: 30px; font-weight: 700; color: var(--brand); line-height: 1; }
  .brand-claim {
    position: absolute; left: 40px; top: 66px;
    font-size: 13px; font-weight: 700; color: var(--brand); letter-spacing: .02em;
  }
  .tagline-band {
    position: absolute; left: 270px; right: 0; top: 40px; height: 42px;
    background: linear-gradient(90deg, var(--orange-light), var(--orange) 40%, var(--orange));
    color: #fff; font-size: 22px;
    display: flex; align-items: center; padding-left: 40px;
  }
  .header-rule {
    position: absolute; left: 0; right: 0; top: 92px; height: 6px;
    background: var(--orange);
  }
  .board-decor {
    position: absolute; left: 0; right: 0; bottom: 70px; height: 260px;
    background: linear-gradient(180deg, rgba(217,217,217,0), var(--board-grey));
  }
  .content {
    position: absolute; left: 42px; top: 124px; width: 736px;
    display: flex; flex-direction: column; gap: 18px;
    font-size: 15.5px; line-height: 1.45;
  }
  .content h2 { font-size: 15.5px; font-weight: 700; margin-bottom: 12px; }
  .content p { margin-bottom: 14px; }
  .content p:last-child { margin-bottom: 0; }
  .row-upper, .row-lower {
    display: grid; grid-template-columns: 360px 346px; column-gap: 30px;
    align-items: start;
  }
  .row-upper .column-left { padding-top: 24px; }
  .row-photo {
    display: grid; grid-template-columns: 196px 300px 208px; column-gap: 16px;
    align-items: start;
  }
  .row-lower .column-right { margin-top: -12px; }
  .photo {
    height: 220px;
    background: linear-gradient(135deg, var(--photo-warm), var(--photo-dark));
  }
  .row-lower { position: relative; }
  .footer-line {
    position: absolute; left: 0; right: 0; bottom: 26px;
    text-align: center; font-size: 30px; font-weight: 700;
  }
</style>
</head>
<body>
  <main class="flyer">
    <div class="brand">
      <span class="brand-mark"></span>
      <span class="brand-name">Turm7Zwerge</span>
    </div>
    <div class="brand-claim">Züge für Wolkenkinder</div>
    <div class="tagline-band">Wir bringen Ihr Kind Zug um Zug zum Erfolg</div>
    <div class="header-rule"></div>

    <div class="board-decor" role="img" aria-label="Dekoratives, auslaufendes Schachbrettmuster"></div>

    <div class="content">
      <div class="row-upper">
        <section class="column-left">
          <h2>Unser Angebot</h2>
          <p>Wir sind eine Schachschule für Kinder zwischen 4 und 15 Jahren</p>
          <p>Wir bieten in unserem zentralen Kurslokal in Seeheim, Lindenweg 12:<br>
            tägliches Schachtraining für alle Alters- und Leistungsstufen von Montag bis Freitag zwischen 13.30 und 19.00 Uhr, sowie Samstags von 10.00-12.00 Uhr<br>
            Regelmässige Ferienkurse<br>
            kostenlose PC-Übungsstationen mit diversen Kinder-Schachprogrammen</p>
          <p>Wir bieten im Grossraum Zürich:<br>
            Schachkurse in Kleingruppen auf Deutsch und Englisch in verschiedenen Alter- und</p>
        </section>
        <section class="column-right">
          <h2>Schach macht Spass!</h2>
          <p>Schach ist Magie: Kaum ist das Schachbrett aufgebaut und der erste Zug getan, liegt vor den Kindern ein Meer voller aufregender Geschichten. Die spannenden Figuren und intensiven Kämpfe um Sieg und Niederlage wecken den Abenteuergeist der Kinder, ihre Phantasie wird angeregt und lässt die Kinder nicht mehr los. An Spannung schlägt Schach jedes Computerspiel!</p>
          <h2>Schach macht schlau und aufmerksam!</h2>
          <p>Die positive Wirkung von Schachtraining auf die Intelligenz von Kindern ist vielfach belegt und reicht von der Erhöhung kognitiver und sprachlicher Fähigkeiten über</p>
        </section>
      </div>

      <div class="row-photo">
        <p>Leistungsstufen. Bei Bedarf kommen wir auch in Ihre Nähe.<br>
          Schachkurse und Projekte resp. Schachevents für Schulen und Kindergärten in der gesamten Deutschschweiz</p>
        <div class="photo" role="img" aria-label="Foto: Kinder spielen an einem langen Tisch Schach"></div>
        <p>eine bessere Leistungsmotivation bis hin zu einer gesteigerten Sozialkompetenz. Die Kinder lernen, auch bei Stress und Zeitdruck aufmerksam und konzentriert zu bleiben.</p>
      </div>

      <div class="row-lower">
        <section class="column-left">
          <h2>Warum Kinderschach:</h2>
          <p>Schach ist eine Lebensschule, die das Leben Ihres Kindes nachhaltig positiv verändert. Die Kinder eignen sich spielerisch wesentliche Fähigkeiten an, die sie sowohl im sozialen als auch im schulischen Umfeld zu Höchstleistungen befähigen.</p>
        </section>
        <section class="column-right">
          <h2>Schach macht stark und selbstbewusst!</h2>
          <p>Schach ist lebensnah und vermittelt den Kindern, mit Herausforderungen im Leben konstruktiv umzugehen. Der Umgang mit Erfolgen und Niederlagen hilft, ihr Selbstvertrauen und psychische Stabilität zu stärken.</p>
        </section>
      </div>
    </div>

    <p class="footer-line">Mehr Infos im Internet auf www.turm7zwerge-beispiel.ch</p>
  </main>
</body>
</html>
```